Create Website for new company called "Verdale Lodge 37"

Verdale Lodge 37 is a new business situated in Southwestern Colorado. We are creating a business that will rent out spaces where clients can grow their own marijuana. Picture a large green house with partitioned spaces that are secured by a lock. Best way to envision this would be to think of a storage business that rents out storage rooms. The difference is that we will be having the units inside a green house ( for growing purposes) Picture a small area that is secured by locks, Picture an area that has the ability to provide state of the art security, cameras etc. We want to focus our efforts on professionals, blue collar workers and end users of marijuana. Our emphasis is in the area of assisting those whom wish to grow their own plants. We want to provide them a safe facility in which to do that. . Keep in mind that we also build custom grow rooms at clients homes and provide a grow pod (lease these) where a small grow unit will be delivered and picked up from our clients whom want to lease a unit for a short amount of time. We have a business card ( just designed) and will send that information to those whom express an interests in this project. We want to be able to sign people up for our services by entering an agreement and signing the agreement while on the internet. We want to provide our services to those whom consume recreational and medical marijuana. This site will need to gather information I.e email addresses so that we can followup with offers. This is a tremendous opportunity for the right designer. We will be creating many more websites as other states come on line and make marijuana legal to consume. Use the business card model for a point of reference of how we envision the concept. That is a business card we just recently printed. The hands and the plant is our logo so far. Open to suggestions. There will be three levels of service. Bronze, Silver, Gold or Platinum. We will also have a retail biz down the road but not at the present time.

Target Market(s)

Ages 21-60

Industry/Entity Type

Medical

Logo Text

Verdale Lodge 37.

Number of Pages Required

5+ page

Requirements
Must have
• Clean appearance not to busy , easily navigable from link to link, page to page. Must have ability down the road to enter into a contractual agreement via the website. Must use our provided logo and example of that is on our business card that will be uploaded here shortly. We would like to have the colors that are on the business card however if you have suggestions or color schemes that you want us to consider that is okay.
Nice to have
• Nice to have a animation of seed to weed and how clients can save a tremendous amount of money growing their own cannabis. Nice to have testimonial page or feedback page. Have a membership component to website,
Should not have
• No flashing lights, etc. Not to busy in terms of animations.

```html
<!DOCTYPE html>
<html lang="en">
<head>
<meta charset="utf-8">
<title>Verdale Lodge 37</title>
<link href="https://fonts.googleapis.com/css2?family=Open+Sans:ital,wght@0,400;0,600;0,700;1,400&display=swap" rel="stylesheet">
<style>
:root{
  --orange:#c97a2c;
  --ink:#333;
  --muted:#666;
  --line:#dcdcdc;
  --panel:#ececec;
  --footer:#d9d9d9;
}
*{margin:0;padding:0;box-sizing:border-box}
html,body{width:973px;height:1200px;overflow:hidden;background:#fff}
body{position:relative;font-family:Arial,Helvetica,sans-serif;color:var(--ink)}
.abs{position:absolute}
.header{left:0;top:0;width:973px;height:96px;background:linear-gradient(#fff,#f1f1f1)}
.brand{left:80px;top:46px;display:flex;align-items:center;gap:8px;font-family:"Open Sans",sans-serif;font-weight:700;font-size:27px;color:#3a3a3a;letter-spacing:-.5px}
.brand-dot{width:16px;height:16px;border-radius:50%;background:var(--orange)}
.contact{top:44px;display:flex;align-items:center;gap:9px;font-family:"Open Sans",sans-serif;font-size:13px;color:#555}
.contact .ring{width:34px;height:34px;border:2px solid var(--orange);border-radius:50%;display:flex;align-items:center;justify-content:center}
.nav{left:0;top:96px;width:973px;height:42px;background:linear-gradient(#fafafa,#ececec);border-top:1px solid var(--line);border-bottom:1px solid var(--line)}
.nav a{position:absolute;top:0;height:42px;line-height:42px;text-align:center;font-family:"Open Sans",sans-serif;font-size:9.5px;color:#333;text-decoration:none;border-left:1px solid var(--line)}
.nav a.active{background:#fff;border-bottom:3px solid var(--orange)}
.slider{left:80px;top:158px;width:813px;height:309px;background:linear-gradient(180deg,#aebfcd 0%,#cdd9df 40%,#7fb83c 62%,#5f9e22 100%);box-shadow:0 18px 18px -12px rgba(0,0,0,.35)}
.caption{left:542px;top:315px;width:351px;height:99px;background:rgba(20,20,20,.9);border-left:4px solid var(--orange);text-align:right;padding:14px 27px 0 0}
.caption h2{font-family:"Open Sans",sans-serif;font-weight:600;color:var(--orange);font-size:22px;letter-spacing:.3px}
.caption p{font-family:"Open Sans",sans-serif;color:#fff;font-size:10px;line-height:20px;margin-top:4px;white-space:nowrap}
.arrows{left:837px;top:438px;display:flex;gap:2px}
.arrows span{width:20px;height:19px;background:rgba(40,80,20,.5);display:flex;align-items:center;justify-content:center}
.welcome{left:0;top:515px;width:973px;text-align:center}
.welcome h1{font-family:"Open Sans",sans-serif;font-weight:700;color:var(--orange);font-size:15.5px}
.welcome p{font-size:10px;color:#555;line-height:19.5px;margin-top:10px;white-space:nowrap}
.card{top:615px;width:184px;height:228px;background:var(--panel);border-bottom:3px solid var(--orange)}
.card .photo{height:114px}
.card h3{font-family:"Open Sans",sans-serif;font-weight:700;font-size:10px;color:var(--orange);margin:22px 0 0 19px;white-space:nowrap}
.card p{font-size:8.3px;line-height:16.7px;color:#666;margin:8px 14px 0 19px}
.card.featured{background:var(--orange)}
.card.featured h3,.card.featured p{color:#fff}
.section-title{font-family:"Open Sans",sans-serif;font-weight:700;font-size:10px;color:var(--orange)}
.quote{top:912px;width:213px;height:99px;background:#f1f1f1;border:1px solid #d8d8d8;padding:16px 14px 0 22px;font-size:8.2px;line-height:16px;color:#666}
.author{top:1026px;display:flex;gap:16px}
.author .face{width:46px;height:41px}
.author b{display:block;font-weight:400;color:var(--orange);font-size:10px;margin-top:6px}
.author i{display:block;color:#666;font-size:8.2px;margin-top:5px}
.about{left:569px;top:912px;width:324px}
.about .lead{font-size:10px;line-height:18.5px;color:#333}
.about .body{font-size:8.2px;line-height:16.7px;color:#666;margin-top:6px}
.btn{left:573px;top:1029px;width:88px;height:25px;background:var(--orange);color:#fff;font-size:8.5px;line-height:25px;text-align:center;border-radius:2px}
.footer{left:0;top:1115px;width:973px;height:85px;background:var(--footer)}
.flinks{left:80px;top:1141px;font-family:"Open Sans",sans-serif;font-size:7.8px;color:#333;word-spacing:2px}
.flinks span{margin:0 13px}
.copy{left:80px;top:1165px;font-family:"Open Sans",sans-serif;font-size:7.5px;color:#333}
.social-label{left:622px;top:1153px;font-family:"Open Sans",sans-serif;font-size:7.5px;color:#333}
.dots{left:772px;top:1146px;display:flex;gap:8px}
.dots span{width:24px;height:24px;border-radius:50%;background:#9c9c9c}
</style>
</head>
<body>
<header class="header abs">
  <div class="brand abs"><span class="brand-dot"></span>Verdale Lodge 37</div>
  <div class="contact abs" style="left:542px">
    <span class="ring"><svg width="14" height="14" viewBox="0 0 24 24"><path fill="#c97a2c" d="M6.6 10.8c1.4 2.8 3.8 5.1 6.6 6.6l2.2-2.2c.3-.3.7-.4 1-.2 1.1.4 2.3.6 3.6.6.6 0 1 .4 1 1V20c0 .6-.4 1-1 1C10.6 21 3 13.4 3 4c0-.6.4-1 1-1h3.5c.6 0 1 .4 1 1 0 1.3.2 2.5.6 3.6.1.3 0 .7-.2 1z"/></svg></span>
    <span>(970) 555 0137</span>
  </div>
  <div class="contact abs" style="left:699px">
    <span class="ring"><svg width="13" height="11" viewBox="0 0 24 18"><path fill="#c97a2c" d="M0 0h24v2l-12 8L0 2zM0 4l12 8 12-8v14H0z"/></svg></span>
    <span>hello@verdalelodge37.com</span>
  </div>
</header>

<nav class="nav abs">
  <a class="active" style="left:80px;width:108px">HOME</a>
  <a style="left:188px;width:111px">ABOUT US</a>
  <a style="left:299px;width:118px">SERVICES</a>
  <a style="left:417px;width:114px">PRODUCTS</a>
  <a style="left:531px;width:139px">TESTIMONIALS</a>
  <a style="left:670px;width:126px;border-right:1px solid var(--line)">CONTACT US</a>
</nav>

<div class="slider abs" role="img" aria-label="Interior of a large greenhouse with rows of young green plants"></div>
<div class="caption abs">
  <h2>VERDALE LODGE 37</h2>
  <p>PRIVATE, LOCKED GROW UNITS INSIDE A SECURE GREENHOUSE<br>FOR MEDICAL AND RECREATIONAL GROWERS...</p>
</div>
<div class="arrows abs">
  <span><svg width="6" height="9"><path d="M5 1L1 4.5 5 8" stroke="#ccc" fill="none"/></svg></span>
  <span><svg width="6" height="9"><path d="M1 1l4 3.5L1 8" stroke="#ccc" fill="none"/></svg></span>
</div>

<section class="welcome abs">
  <h1>WELCOME TO VERDALE LODGE 37</h1>
  <p>Rent your own lockable grow unit inside our Southwestern Colorado greenhouse, watched over by cameras and modern security around the clock.<br>Grow your own plants in a safe facility and save a great deal compared with buying from a store.</p>
</section>

<article class="card featured abs" style="left:80px">
  <div class="photo" role="img" aria-label="Close-up of a green plant leaf against a blue sky" style="background:linear-gradient(135deg,#2f4f6f,#7d8f4a 60%,#4b6a8a)"></div>
  <h3>GREENHOUSE GROW UNITS</h3>
  <p>Rent a private, locked space inside our greenhouse, like a storage unit made for growing...</p>
</article>
<article class="card abs" style="left:289px">
  <div class="photo" role="img" aria-label="Polytunnel greenhouse with rows of seedlings" style="background:linear-gradient(180deg,#eef0ee 0%,#d6dcd8 45%,#7ea840 70%,#4d7d22 100%)"></div>
  <h3>CUSTOM GROW ROOMS</h3>
  <p>We design and build custom grow rooms right in your home, fitted to your space...</p>
</article>
<article class="card abs" style="left:498px">
  <div class="photo" role="img" aria-label="Dense green plant foliage" style="background:radial-gradient(circle at 45% 45%,#5c8a35,#203a16 75%)"></div>
  <h3>GROW POD LEASING</h3>
  <p>Lease a small grow pod for a short term. We deliver it and pick it up when you are done...</p>
</article>
<article class="card abs" style="left:709px">
  <div class="photo" role="img" aria-label="Glass greenhouse exterior under blue sky" style="background:linear-gradient(180deg,#2b63c4 0%,#6e98d8 40%,#a8b8c8 60%,#6a7a88 100%)"></div>
  <h3>MEMBERSHIP LEVELS</h3>
  <p>Choose Bronze, Silver, Gold or Platinum and sign your agreement online in minutes...</p>
</article>

<div class="section-title abs" style="left:80px;top:884px">TESTIMONIALS</div>
<svg class="abs" style="left:514px;top:886px" width="18" height="8"><path d="M4 1L1 4l3 3M14 1l3 3-3 3" stroke="#999" fill="none"/></svg>

<blockquote class="quote abs" style="left:80px">Having my own locked unit in the greenhouse changed everything. The space is clean, the cameras give real peace of mind and the staff helped me set up my first grow...</blockquote>
<blockquote class="quote abs" style="left:321px">I leased a grow pod for one season. It arrived ready to go, was picked up on time and I saved far more than I expected by growing my own plants at home...</blockquote>
<div class="author abs" style="left:80px">
  <div class="face" role="img" aria-label="Portrait photo of the reviewer" style="background:linear-gradient(#4a8cc0,#c9a080)"></div>
  <div><b>Elliot Marsh</b><i>Marketing Executive</i></div>
</div>
<div class="author abs" style="left:321px">
  <div class="face" role="img" aria-label="Portrait photo of the reviewer" style="background:linear-gradient(#f2f2f2,#b8c8d8)"></div>
  <div><b>Elliot Marsh</b><i>Marketing Executive</i></div>
</div>

<div class="section-title abs" style="left:569px;top:884px">ABOUT VERDALE LODGE 37</div>
<div class="about abs">
  <p class="lead">A safe, secure place for adults 21 and over to grow their own.<br>Serving medical and recreational growers.</p>
  <p class="body">Verdale Lodge 37 rents private grow units inside a secured greenhouse in Southwestern Colorado. We also build custom grow rooms and lease grow pods. Join with your email to get member offers and pick the Bronze, Silver, Gold or Platinum plan that fits you...</p>
</div>
<div class="btn abs">READ MORE</div>

<footer class="footer abs"></footer>
<div class="flinks abs">HOME<span>/</span>ABOUT US<span>/</span>SERVICES<span>/</span>PRODUCTS<span>/</span>TESTIMONIALS<span>/</span>CONTACT US</div>
<div class="copy abs">COPYRIGHT 2014. VERDALE LODGE 37. ALL RIGHTS RESERVED.</div>
<div class="social-label abs">CONNECT WITH OUR SOCIAL NETWORK :</div>
<div class="dots abs"><span></span><span></span><span></span><span></span></div>
</body>
</html>
```